Velmora Consulting Business

** Please add the content information from my old business card
1. I would like to see a two sided business card with both options with the 1st Option--Tallow Spire-new WHITE BACKGROUND LOGO
2 nd Option-Tallow Spire - new BLACK- Background Logo
3rd -Option a business card with my Photo on the card
Please add the new word to the card information:
EXECUTION
AS THE OWNER'S REP
WE AIM TO ACHIEVE YOUR
INFRASTRUCTURE VISION with
OUR SPECIALIZATION & EXECUTION in:

FUNDING Planning
BUSINESS Planning
INFRASTRUCTURE Planning
PROJECT Management
Since 2012
_____________________________________________________________________
I want to get spot uv raised printing. I was liking a a nice rich white linen paper stock with black writing & NOT A COLORED CARD other than a variety of white or black cards concept

```html
<!DOCTYPE html>
<html lang="en">
<head>
<meta charset="utf-8">
<title>Velmora Consulting – Business Card</title>
<link rel="stylesheet" href="https://fonts.googleapis.com/css2?family=Source+Sans+3:wght@400;600;700&display=swap">
<style>
  :root {
    --backdrop: #1b1b1b;
    --card-black: #252324;
    --card-white: #f4f4f2;
    --ink: #111111;
    --ink-light: #ffffff;
    --accent-red: #e31b3b;
    --mark-grey-dark: #3a3839;
    --mark-grey-light: #c9c9c9;
  }
  * { box-sizing: border-box; margin: 0; padding: 0; }
  html, body { width: 1200px; height: 1015px; overflow: hidden; }
  body {
    background: var(--backdrop);
    font-family: "Source Sans 3", "Myriad Pro", sans-serif;
    display: flex;
    flex-direction: column;
    align-items: center;
    justify-content: center;
    gap: 60px;
  }
  .card {
    width: 640px;
    height: 366px;
    position: relative;
    overflow: hidden;
  }

  /* Back side */
  .card--back { background: var(--card-black); color: var(--ink-light); }
  .mission {
    position: absolute;
    top: 34px;
    right: 40px;
    text-align: right;
    font-size: 15px;
    line-height: 1.18;
    letter-spacing: 0.2px;
  }
  .services { list-style: none; margin-top: 16px; }
  .services li { display: flex; justify-content: flex-end; align-items: center; gap: 6px; }
  .services li::after {
    content: "";
    width: 7px; height: 7px;
    background: var(--accent-red);
    display: inline-block;
  }
  .since { margin-top: 8px; }
  .back-name {
    position: absolute;
    left: 44px;
    bottom: 44px;
    font-size: 46px;
    font-weight: 700;
    line-height: 1;
    color: var(--mark-grey-dark);
  }

  /* Front side */
  .card--front { background: var(--card-white); color: var(--ink); }
  .brand {
    position: absolute;
    top: 50px;
    right: 44px;
    display: flex;
    align-items: center;
    gap: 12px;
    font-size: 34px;
    font-weight: 600;
    color: var(--mark-grey-light);
  }
  .brand__square { width: 18px; height: 18px; background: var(--accent-red); }
  .details {
    position: absolute;
    left: 56px;
    bottom: 24px;
    display: flex;
    flex-direction: column;
    gap: 18px;
  }
  .person__name { font-size: 24px; font-weight: 700; line-height: 1.1; }
  .person__title { font-size: 16px; line-height: 1.3; color: var(--accent-red); letter-spacing: 0.3px; }
  .contact { list-style: none; font-size: 16px; line-height: 1.45; }
  .contact li { display: flex; align-items: center; gap: 10px; }
  .contact svg { width: 14px; height: 14px; fill: none; stroke: var(--accent-red); stroke-width: 2; }
  .locations { font-size: 16px; line-height: 1.3; }
</style>
</head>
<body>

  <section class="card card--back" aria-label="Card back">
    <div class="mission">
      <p>EXECUTION<br>AS THE OWNER'S REP<br>WE AIM TO ACHIEVE YOUR<br>INFRASTRUCTURE VISION with<br>OUR SPECIALIZATION &amp; EXECUTION in:</p>
      <ul class="services">
        <li>FUNDING Planning</li>
        <li>BUSINESS Planning</li>
        <li>INFRASTRUCTURE Planning</li>
        <li>PROJECT Management</li>
      </ul>
      <p class="since">Since 2012</p>
    </div>
    <p class="back-name">Velmora Consulting</p>
  </section>

  <section class="card card--front" aria-label="Card front">
    <div class="brand">
      <span class="brand__square"></span>
      <span>Velmora Consulting</span>
    </div>
    <div class="details">
      <div class="person">
        <p class="person__name">Marisol Quentrell-Ayodeji</p>
        <p class="person__title">CEO / LEAD PROJECT MANAGER</p>
      </div>
      <ul class="contact">
        <li>
          <svg viewBox="0 0 16 16" aria-hidden="true"><path d="M3 2l3 1 1 3-2 1a8 8 0 0 0 4 4l1-2 3 1 1 3-2 1C7 14 2 9 2 4z"/></svg>
          867.555.0182
        </li>
        <li>
          <svg viewBox="0 0 16 16" aria-hidden="true"><rect x="1.5" y="3.5" width="13" height="9"/><path d="M1.5 3.5l6.5 5 6.5-5"/></svg>
          mari@velmora.ca
        </li>
        <li>
          <svg viewBox="0 0 16 16" aria-hidden="true"><circle cx="8" cy="8" r="6.5"/><path d="M1.5 8h13M8 1.5c-3 3-3 10 0 13M8 1.5c3 3 3 10 0 13"/></svg>
          www.velmora.ca
        </li>
      </ul>
      <p class="locations">Norhaven NT • Calderbrook NB</p>
    </div>
  </section>

</body>
</html>
```